Kinesiology undergraduate program needs an infographic

We would like an infographic to creatively and succinctly inform students, faculty, staff, and others about our undergraduate values and competencies (perhaps also integrating our mission and vision). We would like to see a design that incorporates the definition of Kinesiology (the study of human movement) and the colors of our Westbrook State University at Harlan.

```html
<!DOCTYPE html>
<html lang="en">
<head>
<meta charset="utf-8">
<title>Kinesiology Undergraduate Values, Mission and Vision</title>
<link rel="stylesheet" href="https://fonts.googleapis.com/css2?family=Bowlby+One&family=Montserrat:wght@800&family=Poppins:wght@400&display=swap">
<style>
  :root {
    --red: #d6001c;
    --navy: #1c2340;
    --ink: #1f1f24;
    --grey-disc: #ececee;
    --white: #ffffff;
  }
  * { margin: 0; padding: 0; box-sizing: border-box; }
  html, body { width: 1200px; height: 848px; overflow: hidden; background: var(--white); }
  .infographic { position: relative; width: 1200px; height: 848px; font-family: "Poppins", sans-serif; color: var(--ink); }
  .abs { position: absolute; }

  .department { left: 39px; top: 40px; font-family: "Montserrat", sans-serif; font-weight: 800; font-size: 11.5px; line-height: 13px; color: var(--red); }

  .headline { font-family: "Bowlby One", sans-serif; color: var(--red); font-size: 41.5px; line-height: 53px; text-align: center; letter-spacing: 0.5px; }
  .statement { font-size: 17px; line-height: 21px; text-align: center; color: var(--ink); }

  .disc { left: 368px; top: 262px; width: 414px; height: 414px; border-radius: 50%; background: var(--grey-disc); }
  .figure { left: 432px; top: 240px; width: 290px; height: 575px; border-radius: 140px 140px 36px 36px;
            background: linear-gradient(90deg, #1d4660 0%, #0f3a55 49%, #c9705a 51%, #d98a6c 100%); opacity: .9; }
  .divider { left: 573px; top: 228px; width: 4px; height: 597px; background: var(--navy); }

  .competency h3 { font-family: "Montserrat", sans-serif; font-weight: 800; font-size: 16.8px; line-height: 21px; color: var(--navy); letter-spacing: .2px; }
  .competency ul { list-style: none; margin-top: 1px; }
  .competency li { font-size: 17.1px; line-height: 21px; position: relative; white-space: nowrap; }
  .competency li::before { content: ""; position: absolute; left: -15px; top: 9px; width: 4px; height: 4px; border-radius: 50%; background: var(--ink); }

  .connectors, .icons { left: 0; top: 0; }
</style>
</head>
<body>
<main class="infographic">

  <div class="department abs">MOVEMENT SCIENCE<br>DEPARTMENT<br>SCHOOL OF<br>HEALTH PROFESSIONS<br>WSUH</div>

  <div class="disc abs"></div>
  <div class="figure abs" role="img" aria-label="Illustrated graduate in cap and gown holding a dumbbell, split down the middle to reveal the human muscular system"></div>
  <div class="divider abs"></div>

  <section class="abs" style="left:377px; top:33px; width:400px;">
    <h1 class="headline">OUR<br>MISSION</h1>
    <p class="statement">To empower undergraduate students<br>to pursue excellence through<br>scientific discovery, clinical practice,<br>and health promotion</p>
  </section>

  <section class="abs" style="left:55px; top:132px; width:300px;">
    <h2 class="headline">OUR<br>VALUES</h2>
    <p class="statement" style="margin-top:-4px;">Student Success, Science,<br>and Service<br>Our Graduates Will Be<br>Competent In...</p>
  </section>

  <section class="abs" style="left:795px; top:145px; width:300px;">
    <h2 class="headline">OUR<br>VISION</h2>
    <p class="statement" style="margin-top:-5px;">WSUH Kinesiology graduates are<br>leaders who excel in careers that<br>enhance the quality of life of<br>individuals and communities</p>
  </section>

  <svg class="connectors abs" width="1200" height="848" aria-hidden="true">
    <polygon points="184,333 203,333 193,349" fill="var(--navy)"/>
    <g fill="none" stroke="var(--navy)" stroke-width="1.2">
      <polyline points="329,392 260,392 260,484"/>
      <polyline points="387,608 358,608 358,664 278,664"/>
      <polyline points="763,379 783,379 783,492 814,492"/>
      <polyline points="724,570 779,570 779,663 817,663"/>
    </g>
    <g fill="var(--ink)">
      <circle cx="329" cy="392" r="3.5"/><circle cx="260" cy="484" r="3.5"/>
      <circle cx="387" cy="608" r="3.5"/><circle cx="278" cy="664" r="3.5"/>
      <circle cx="763" cy="379" r="3.5"/><circle cx="814" cy="492" r="3.5"/>
      <circle cx="724" cy="570" r="3.5"/><circle cx="817" cy="663" r="3.5"/>
    </g>
  </svg>

  <svg class="icons abs" width="1200" height="848" aria-hidden="true" fill="none" stroke="var(--navy)" stroke-width="3" stroke-linejoin="round" stroke-linecap="round">
    <polyline points="86,421 110,421 115,410 121,430 126,392 131,449 137,412 141,421 160,421"/>
    <g transform="translate(80,616)">
      <path d="M8 2 L52 44 L50 52 L42 50 L0 8 Z"/>
      <line x1="42" y1="50" x2="50" y2="42"/>
      <line x1="4" y1="12" x2="12" y2="4"/>
    </g>
    <g transform="translate(1078,436)">
      <path d="M36 12 C22 12 14 22 14 33 C14 42 20 47 24 53 L24 60 L48 60 L48 53 C52 47 58 42 58 33 C58 22 50 12 36 12 Z"/>
      <line x1="26" y1="66" x2="46" y2="66"/><line x1="29" y1="72" x2="43" y2="72"/>
      <line x1="36" y1="0" x2="36" y2="5"/><line x1="12" y1="8" x2="16" y2="12"/><line x1="60" y1="8" x2="56" y2="12"/>
      <line x1="0" y1="31" x2="6" y2="31"/><line x1="66" y1="31" x2="72" y2="31"/>
      <line x1="2" y1="18" x2="7" y2="21"/><line x1="70" y1="18" x2="65" y2="21"/>
    </g>
    <g transform="translate(1072,572)">
      <path d="M26 3 C12 3 3 12 3 23 C3 29 6 34 10 38 L7 48 L19 42 C21 43 24 43 26 43 C40 43 50 34 50 23 C50 12 40 3 26 3 Z"/>
      <line x1="16" y1="17" x2="37" y2="17"/><line x1="16" y1="24" x2="37" y2="24"/><line x1="16" y1="31" x2="30" y2="31"/>
      <path d="M53 22 C63 25 70 32 70 41 C70 46 68 50 64 53 L67 64 L55 58 C52 59 49 59 46 59 C38 59 31 55 28 50"/>
      <line x1="46" y1="44" x2="60" y2="44"/>
    </g>
  </svg>

  <section class="competency abs" style="left:78px; top:457px;">
    <h3>THE SCIENCE OF<br>KINESIOLOGY</h3>
    <ul><li>Foundational Concepts of Kinesiology</li><li>Clinical Application</li><li>Scientific Communication</li></ul>
  </section>

  <section class="competency abs" style="left:78px; top:679px;">
    <h3>INTRAPERSONAL GROWTH</h3>
    <ul><li>Cultural Humility/Sensitivity</li><li>Integrity</li><li>Self-Directed</li><li>Dependability</li><li>Mission Oriented</li></ul>
  </section>

  <section class="competency abs" style="left:841px; top:487px;">
    <h3>THINKING AND REASONING</h3>
    <ul><li>Critical Thinking</li><li>Quantitative Reasoning</li><li>Scientific Inquiry</li><li>Concept Integration</li></ul>
  </section>

  <section class="competency abs" style="left:841px; top:650px;">
    <h3>SERVICE ORIENTATION/CITIZENSHIP</h3>
    <ul><li>Cultural Competence</li><li>Professionalism</li><li>Leadership and Teamwork</li><li>Service Orientation/Citizenship</li></ul>
  </section>

</main>
</body>
</html>
```